Sustainably Transforming Education

Company is education services based. early learning through adult and corporate. Focus is national government policy and program design and delivery alongside a research based and academically grounded set of approaches to planning, evaluation, and change management.I am looking for an innovative design position that aligns with the global agendas for innovation, creativity and collaboration at international and national policy levels (berulo is a name that reflects these qualities - colours need to reflect amythyst in some way). I also need a design that translates from a business card as 1 medium of interaction to a template that can work in word/powerpoint etc to support both stationery as well as a digital strategy across multiple channels (fb/twit/etc)There is no slogan/tag line for the company and their is no logo. I was looking to just leverage the name - have currently played around with various fonts (ending up with cuisine - all lowercase).

Industry/Entity Type

Adult

Contact Information for Business Card

name: berulo (all lowercase)Chairman: Andrew CrowMobile: +61 418 902 131Web: www.berulo.comemail: martin.pelly@berulo-example.com

Font styles to use
Script
Other font styles liked:
• cuisine

Colors
e34298
e667a6
33a6d7
aaaaaa

Requirements
Nice to have
• https://files.example-share.net/sh/qx7kw2hd91lzmnp/AAFr3tYbQeLp8VwZnKcDs2Hu?dl=0
• Link to the printwell templates used to begin this process....the one with the lines was about people intersecting (collaborating).....the organic shapes one more of a fluid feel of people coming together - the overall shape being largely spherical could represent a "global" feel.....anyway that is how I was thinking about these

```html
<!DOCTYPE html>
<html lang="en">
<head>
<meta charset="UTF-8">
<title>berulo — card front</title>
<link rel="stylesheet" href="https://fonts.googleapis.com/css2?family=Kaushan+Script&display=swap">
<style>
  :root {
    --sky: #33a6d7;
    --sky-soft: #74b9e2;
    --amethyst: #e34298;
    --silver: #aaaaaa;
    --white: #ffffff;
  }
  html, body {
    margin: 0;
    padding: 0;
    width: 1200px;
    height: 740px;
    overflow: hidden;
    background: var(--sky);
  }
  .card-front {
    position: relative;
    width: 1200px;
    height: 740px;
    background: var(--sky);
    overflow: hidden;
  }
  .card-front__shapes {
    position: absolute;
    inset: 0;
    width: 1200px;
    height: 740px;
  }
  .shape--pink { fill: var(--amethyst); }
  .shape--silver { fill: var(--silver); }
  .world-area {
    position: absolute;
    left: 324px;
    top: 96px;
    width: 744px;
    height: 480px;
    border-radius: 50%;
    background: radial-gradient(ellipse at center, rgba(116,185,226,0.85) 0%, rgba(116,185,226,0.55) 55%, rgba(116,185,226,0) 72%);
  }
  .wordmark {
    position: absolute;
    left: 0;
    top: 268px;
    width: 1362px;
    margin: 0;
    text-align: center;
    font-family: "Kaushan Script", cursive;
    font-weight: 400;
    font-size: 100px;
    line-height: 1;
    color: var(--white);
    letter-spacing: 2px;
  }
</style>
</head>
<body>
  <main class="card-front">
    <svg class="card-front__shapes" viewBox="0 0 1200 740" aria-hidden="true">
      <path class="shape--pink" d="M0,150 C150,380 300,580 468,740 L0,740 Z"/>
      <path class="shape--silver" d="M26,0 L54,0 C130,320 350,590 618,740 L546,740 C300,590 100,330 26,0 Z"/>
      <path class="shape--silver" d="M114,318 C190,410 260,475 330,525 C250,470 175,400 114,318 Z"/>
    </svg>
    <div class="world-area" role="img" aria-label="Faint world map silhouette in light blue"></div>
    <h1 class="wordmark">berulo</h1>
  </main>
</body>
</html>
```